Web Developer Needs a Business Card Design

I need a personal business card design that represents me as a web developer for potential employers. I would like the background to be a dark color on the front for contrast with my logo and name. The back will have all my information along with a smaller version of the logo. I want something with a modern look and feel, not too conservative. This will be used for potential employers and freelance work.

Industry/Entity Type

Business

Contact Information for Business Card

Front should have my logo and name. The back should have all my personal information which would include: name: Tom Varulek, phone: 570-614-3098, email: tomvarulek@quillbox.net, website url: www.tomvarulek.net, logo, web developer.

Font styles to use
Sans Serif

Requirements
Must have
• Must include my logo. The color palette base color will be the logo color.

```html
<!DOCTYPE html>
<html lang="en">
<head>
<meta charset="utf-8">
<title>Tom Varulek — Business Card</title>
<link href="https://fonts.googleapis.com/css2?family=Open+Sans:wght@400;600;700&display=swap" rel="stylesheet">
<style>
  :root {
    --backdrop: #8c8c8c;
    --card-black: #000000;
    --contact-band: #121212;
    --mint: #4fe3c1;
    --mint-soft: #5fcfb6;
    --paper: #f2f2f2;
    --ink-light: #ffffff;
  }
  * { box-sizing: border-box; margin: 0; padding: 0; }
  html, body {
    width: 1200px; height: 900px; overflow: hidden;
    background: var(--backdrop);
    font-family: "Open Sans", sans-serif;
  }
  .canvas {
    width: 1200px; height: 900px;
    display: flex; flex-direction: column; align-items: center; justify-content: center;
    gap: 60px;
  }
  .card {
    position: relative;
    width: 630px; height: 360px;
    background: var(--card-black);
    overflow: hidden;
    box-shadow: 0 6px 18px rgba(0,0,0,0.35);
  }

  /* Front */
  .front-wordmark {
    position: absolute; left: 44px; top: 60px;
    color: var(--mint);
    font-weight: 700; font-size: 58px; line-height: 1;
    letter-spacing: -1px;
  }
  .front-identity {
    position: absolute; right: 40px; top: 232px;
    text-align: right;
  }
  .front-identity .name {
    color: var(--ink-light);
    font-weight: 700; font-size: 24px; letter-spacing: 2px;
    text-transform: uppercase;
  }
  .front-identity .role {
    color: var(--mint);
    font-weight: 400; font-size: 17px; margin-top: 2px;
  }
  .front .stripe-white { position: absolute; left: 0; right: 0; top: 314px; height: 9px; background: var(--paper); }
  .front .stripe-mint  { position: absolute; left: 0; right: 0; top: 323px; height: 28px; background: var(--mint); }
  .front .stripe-edge  { position: absolute; left: 0; right: 0; top: 351px; height: 9px; background: var(--paper); }

  /* Back */
  .back-wordmark {
    position: absolute; left: 44px; top: 70px;
    color: var(--mint-soft);
    font-weight: 700; font-size: 34px; line-height: 1;
  }
  .back-identity {
    position: absolute; right: 36px; top: 46px;
    text-align: right;
  }
  .back-identity .name {
    color: var(--mint-soft);
    font-weight: 700; font-size: 22px;
  }
  .back-identity .role {
    color: var(--ink-light);
    font-weight: 400; font-size: 17px; margin-top: -2px;
  }
  .contact-band {
    position: absolute; left: 0; right: 0; top: 196px; height: 104px;
    background: var(--contact-band);
  }
  .contact {
    position: absolute;
    display: flex; align-items: center; gap: 6px;
    color: var(--ink-light);
    font-size: 14px;
  }
  .contact svg { width: 13px; height: 13px; flex: none; }
  .contact.phone { left: 28px; top: 18px; }
  .contact.email { left: 215px; top: 44px; }
  .contact.web   { left: 420px; top: 70px; }
  .back .stripe-white { position: absolute; left: 0; right: 0; top: 300px; height: 9px; background: var(--paper); }
  .back .stripe-mint  { position: absolute; left: 0; right: 0; top: 309px; height: 36px; background: var(--mint); }
  .back .stripe-edge  { position: absolute; left: 0; right: 0; top: 345px; height: 15px; background: var(--paper); }
</style>
</head>
<body>
<main class="canvas">

  <section class="card front" aria-label="Business card front">
    <div class="front-wordmark">Tom Varulek</div>
    <div class="front-identity">
      <div class="name">Tom Varulek</div>
      <div class="role">Front-End Developer</div>
    </div>
    <div class="stripe-white"></div>
    <div class="stripe-mint"></div>
    <div class="stripe-edge"></div>
  </section>

  <section class="card back" aria-label="Business card back">
    <div class="back-wordmark">Tom Varulek</div>
    <div class="back-identity">
      <div class="name">Tom Varulek</div>
      <div class="role">Front-End Developer</div>
    </div>

    <div class="contact-band">
      <div class="contact phone">
        <svg viewBox="0 0 16 16" aria-hidden="true"><path fill="#4fe3c1" d="M3 1h3l1.5 4-2 1.3a9 9 0 0 0 4.2 4.2L11 8.5l4 1.5v3a2 2 0 0 1-2 2A12 12 0 0 1 1 3a2 2 0 0 1 2-2z"/></svg>
        <span>570-614-3098</span>
      </div>
      <div class="contact email">
        <svg viewBox="0 0 16 16" aria-hidden="true"><rect x="1" y="3" width="14" height="10" fill="#4fe3c1"/><path d="M1 3l7 6 7-6" fill="none" stroke="#121212" stroke-width="1.4"/></svg>
        <span>tomvarulek@quillbox.net</span>
      </div>
      <div class="contact web">
        <svg viewBox="0 0 16 16" aria-hidden="true"><g fill="none" stroke="#4fe3c1" stroke-width="2" stroke-linecap="round"><path d="M7 9l2-2"/><path d="M6 6.5L4.5 5a2.5 2.5 0 0 0-3.5 3.5L2.5 10"/><path d="M10 9.5l1.5 1.5a2.5 2.5 0 0 0 3.5-3.5L13.5 6"/></g></svg>
        <span>www.tomvarulek.net</span>
      </div>
    </div>

    <div class="stripe-white"></div>
    <div class="stripe-mint"></div>
    <div class="stripe-edge"></div>
  </section>

</main>
</body>
</html>
```